Weightloss company needs Business Card

We want a business card that is clean and professional, yet portrays that we are a friendly, innovative, and versatile program designed to fit the needs of our clients.
I would like there to be 2 sides, one side having an appointment card, and the other side containing the logo and business information. There can be decorations on both sides. The logo is attached.

Target Market(s)

Men and women 40-60

Industry/Entity Type

Business

Contact Information for Business Card

Font styles to use
Sans Serif

Requirements
Must have
• The logo, space for business information
Nice to have
• The colors in the logo
Should not have
• No pictures of people or food

```html
<!DOCTYPE html>
<html lang="en">
<head>
<meta charset="utf-8">
<title>Turnwell Weightloss – Business &amp; Appointment Card</title>
<link rel="stylesheet" href="https://fonts.googleapis.com/css2?family=Source+Sans+3:wght@400;600;700&display=swap">
<style>
  :root {
    --backdrop: #141414;
    --brand-red: #fb002c;
    --card-white: #ffffff;
    --ink-dark: #111111;
    --text-light: #ffffff;
  }
  * { margin: 0; padding: 0; box-sizing: border-box; }
  html, body {
    width: 1200px;
    height: 900px;
    overflow: hidden;
    background: var(--backdrop);
    font-family: "Source Sans 3", Arial, sans-serif;
  }
  .canvas {
    position: relative;
    width: 1200px;
    height: 900px;
    background: var(--backdrop);
  }
  .card {
    position: absolute;
    top: 184px;
    width: 302px;
    height: 491px;
    border-radius: 14px;
    text-align: center;
  }
  .card--contact {
    left: 299px;
    background: var(--brand-red);
    color: var(--text-light);
  }
  .card--appointment {
    left: 645px;
    width: 305px;
    background: var(--card-white);
    color: var(--brand-red);
  }
  .brand-name {
    position: absolute;
    left: 0;
    right: 0;
    font-weight: 700;
    font-size: 30px;
    line-height: 30px;
    letter-spacing: 0.3px;
  }
  .card--contact .brand-name { top: 80px; color: var(--text-light); }
  .card--appointment .brand-name { top: 66px; color: var(--brand-red); }

  .person {
    position: absolute;
    top: 266px;
    left: 0;
    right: 0;
  }
  .person__name {
    font-weight: 600;
    font-size: 21.5px;
    line-height: 26px;
  }
  .person__role {
    font-size: 16.5px;
    line-height: 20px;
  }
  .contact-list {
    position: absolute;
    top: 341px;
    left: 0;
    right: 0;
    list-style: none;
    font-size: 16px;
    line-height: 20px;
  }
  .contact-list li {
    display: flex;
    justify-content: center;
    align-items: center;
    gap: 9px;
  }
  .contact-list svg { width: 10px; height: 10px; fill: var(--text-light); }
  .address {
    position: absolute;
    top: 419px;
    left: 0;
    right: 0;
    font-style: normal;
    font-size: 15.5px;
    line-height: 17px;
  }

  .appointment__title {
    position: absolute;
    top: 229px;
    left: 0;
    right: 0;
    font-weight: 600;
    font-size: 22px;
  }
  .appointment__fields {
    position: absolute;
    top: 286px;
    left: 37px;
    right: 38px;
    list-style: none;
    text-align: left;
  }
  .field {
    display: flex;
    align-items: baseline;
    height: 37px;
    font-size: 16px;
    font-weight: 700;
  }
  .field__label { color: var(--brand-red); margin-right: 4px; }
  .field__line {
    flex: 1;
    border-bottom: 2px dotted var(--ink-dark);
    transform: translateY(-3px);
  }
  .field__unit { color: var(--ink-dark); font-weight: 600; }
  .notice {
    position: absolute;
    top: 415px;
    left: 0;
    right: 0;
    font-weight: 700;
    font-size: 15px;
    line-height: 19px;
    text-transform: uppercase;
  }
</style>
</head>
<body>
<div class="canvas">

  <section class="card card--contact" aria-label="Business card front">
    <div class="brand-name">Turnwell<br>Weightloss</div>

    <div class="person">
      <p class="person__name">DANIEL REYES</p>
      <p class="person__role">Managing Director</p>
    </div>

    <ul class="contact-list">
      <li>
        <svg viewBox="0 0 10 10" aria-hidden="true"><path d="M1 3 Q5 0 9 3 L8 4.5 L6.5 4 L6.5 3 Q5 2.6 3.5 3 L3.5 4 L2 4.5 Z M2.5 5 L7.5 5 L8.5 9 L1.5 9 Z"/></svg>
        <span>555-014-2398</span>
      </li>
      <li>
        <svg viewBox="0 0 10 10" aria-hidden="true"><path d="M0.5 2 H9.5 V8.5 H0.5 Z" /><path d="M0.5 2 L5 5.5 L9.5 2" stroke="#fb002c" stroke-width="1" fill="none"/></svg>
        <span>hello@turnwell.com</span>
      </li>
    </ul>

    <address class="address">
      5678, Placeholder Road<br>
      Region Name, 654321
    </address>
  </section>

  <section class="card card--appointment" aria-label="Appointment card back">
    <div class="brand-name">Turnwell<br>Weightloss</div>

    <h2 class="appointment__title">Your Next Appointment is</h2>

    <ul class="appointment__fields">
      <li class="field"><span class="field__label">Name:</span><span class="field__line"></span></li>
      <li class="field"><span class="field__label">Date:</span><span class="field__line"></span></li>
      <li class="field">
        <span class="field__label">Time:</span><span class="field__line"></span>
        <span class="field__unit">AM</span><span class="field__line"></span>
        <span class="field__unit">PM</span>
      </li>
    </ul>

    <p class="notice">If unable to keep appointment,<br>kindly give 24hrs notice.</p>
  </section>

</div>
</body>
</html>
```